BOLD & MINIMALIST DESIGN NEEDED

We want a very bold but minimalistic business card design that is impactful and utilizes both sides of the business card. Our current logo is included for your use.

We want bold fonts and good use of negative space. We don't want the logo to overpower the design.

Target Market(s)

Professionals who are building new commercial buildings.

Industry/Entity Type

Construction

Contact Information for Business Card

Name, Title, email, office phone, cell phone, website

Font styles to use
Serif
Sans Serif

Requirements
Must have
• Bold design!

```html
<!DOCTYPE html>
<html lang="en">
<head>
<meta charset="utf-8">
<title>Summitvale Business Card</title>
<link rel="stylesheet" href="https://fonts.googleapis.com/css2?family=Montserrat:wght@400;500;800&display=swap">
<style>
  :root {
    --stage: #3b3b3d;
    --card-dark: #0b0b0c;
    --card-light: #ffffff;
    --ink: #111111;
    --green: #7fc32a;
    --muted: #9a9a9a;
    --dark-name: #2a2a2c;
  }
  * { margin: 0; padding: 0; box-sizing: border-box; }
  html, body { width: 1200px; height: 689px; overflow: hidden; }
  body {
    background: var(--stage);
    font-family: "Montserrat", sans-serif;
    position: relative;
  }
  .card {
    position: absolute;
    top: 190px;
    width: 560px;
    height: 310px;
    border-radius: 20px;
    overflow: hidden;
    box-shadow: 0 18px 40px rgba(0,0,0,.45);
  }
  .card--back { left: 25px; background: var(--card-dark); }
  .card--front { left: 615px; background: var(--card-light); }

  .brand {
    position: absolute;
    display: flex;
    align-items: center;
    gap: 10px;
    white-space: nowrap;
  }
  .brand__mark { width: 20px; height: 20px; background: var(--green); }
  .brand__name { font-weight: 800; letter-spacing: 1px; }

  .card--back .brand { left: 50%; top: 50%; transform: translate(-50%, -50%); gap: 12px; }
  .card--back .brand__name { font-size: 44px; color: var(--dark-name); }
  .card--back .brand__mark { background: var(--dark-name); width: 30px; height: 30px; }

  .card--front .brand { left: 32px; top: 130px; }
  .card--front .brand__name { font-size: 24px; color: var(--ink); }

  .divider {
    position: absolute;
    left: 268px; top: 42px;
    width: 1px; height: 150px;
    background: var(--muted);
  }
  .contact { position: absolute; left: 290px; top: 46px; }
  .contact__name { font-weight: 800; font-size: 20px; color: var(--ink); letter-spacing: .5px; white-space: nowrap; }
  .contact__title { font-weight: 500; font-size: 14px; color: var(--green); margin-top: 2px; }
  .contact__list { list-style: none; margin-top: 16px; }
  .contact__item {
    display: flex; align-items: center; gap: 9px;
    font-size: 13px; color: var(--ink); line-height: 22px;
    white-space: nowrap;
  }
  .contact__icon { width: 13px; height: 13px; flex: none; }

  .swoosh { position: absolute; left: 0; bottom: 0; width: 560px; height: 310px; }
</style>
</head>
<body>
  <section class="card card--back" aria-label="Card back">
    <div class="brand">
      <span class="brand__mark"></span>
      <span class="brand__name">SUMMITVALE</span>
    </div>
  </section>

  <section class="card card--front" aria-label="Card front">
    <svg class="swoosh" viewBox="0 0 560 310" aria-hidden="true">
      <path d="M240 310 C350 278 460 232 560 205 L560 310 Z" fill="#111111"/>
      <path d="M360 268 C440 238 510 212 560 200 L560 220 C500 234 430 258 360 288 Z" fill="#7fc32a"/>
    </svg>

    <div class="brand">
      <span class="brand__mark"></span>
      <span class="brand__name">SUMMITVALE</span>
    </div>

    <div class="divider"></div>

    <div class="contact">
      <p class="contact__name">MARCUS ELLERY</p>
      <p class="contact__title">Managing Director</p>
      <ul class="contact__list">
        <li class="contact__item">
          <svg class="contact__icon" viewBox="0 0 16 16"><path d="M3 1h3l1.5 4-2 1.5a9 9 0 0 0 4 4L11 8.5l4 1.5v3a2 2 0 0 1-2 2C7 15 1 9 1 3a2 2 0 0 1 2-2z" fill="#7fc32a"/></svg>
          044-555 018 204
        </li>
        <li class="contact__item">
          <svg class="contact__icon" viewBox="0 0 16 16"><rect x="4" y="1" width="8" height="14" rx="1.5" fill="none" stroke="#7fc32a" stroke-width="1.8"/></svg>
          044-555 018 205
        </li>
        <li class="contact__item">
          <svg class="contact__icon" viewBox="0 0 16 16"><rect x="1" y="3" width="14" height="10" fill="#7fc32a"/><path d="M1 3l7 6 7-6" fill="none" stroke="#fff" stroke-width="1.4"/></svg>
          hello@summitvale.com
        </li>
        <li class="contact__item">
          <svg class="contact__icon" viewBox="0 0 16 16"><circle cx="8" cy="8" r="7" fill="#7fc32a"/><path d="M1 8h14M8 1c-3 3-3 11 0 14M8 1c3 3 3 11 0 14" fill="none" stroke="#fff" stroke-width="1"/></svg>
          www.summitvale.com
        </li>
      </ul>
    </div>
  </section>
</body>
</html>
```